Meridian Crestline Motors *

Professional business cards for our auto wholesale dealership.

Target Market(s)

New and used cars sales managers and middle class to higher end private party buyers.

Industry/Entity Type

Automotive

Contact Information for Business Card

Meridian Crestline Motors
Darnell R Okonski
Owner
(555) 304-6618
mercrestmotors@quillbox.example
Dealer Lic # 48265

Logo Text

Meridian Crestline Motors, Mer Crest Motors, MCM, etc

Font styles to use
Serif
Sans Serif

Colors

Designer to choose colors to be used in the design.

Requirements
Must have
• A professional, but not pretentious, look
Nice to have
• It might be nice to see "MCM" in a shape form i.e. circle, triangle, etc in the corner or background somehwere
Should not have
• bright "girly" colors

```html
<!DOCTYPE html>
<html lang="en">
<head>
<meta charset="utf-8">
<title>Meridian Crestline Motors – Business Card</title>
<link href="https://fonts.googleapis.com/css2?family=Ubuntu:wght@400;500;700&display=swap" rel="stylesheet">
<style>
  :root {
    --page-bg: #3a3d41;
    --card-top: #262a30;
    --card-bottom: #1d2025;
    --lime: #a4c812;
    --lime-deep: #8fb00c;
    --ink-light: #ffffff;
    --ink-soft: #e6e8ea;
  }
  * { margin: 0; padding: 0; box-sizing: border-box; }
  html, body { width: 1200px; height: 1200px; overflow: hidden; }
  body {
    background: var(--page-bg);
    font-family: "Ubuntu", sans-serif;
    position: relative;
  }
  .card {
    position: absolute;
    left: 214px;
    width: 818px;
    height: 470px;
    border-radius: 22px;
    overflow: hidden;
    background: radial-gradient(ellipse at 55% 30%, var(--card-top), var(--card-bottom) 80%);
  }
  .card--front { top: 125px; }
  .card--back { top: 617px; }

  .rule-thin {
    position: absolute; left: 0; right: 0; height: 4px; background: var(--lime);
  }
  .band-base {
    position: absolute; left: 0; right: 0; bottom: 0; height: 24px;
    background: linear-gradient(90deg, var(--lime-deep), var(--lime) 50%, var(--lime-deep));
  }

  /* Front */
  .front-mark {
    position: absolute; left: 82px; top: 128px;
    width: 186px; height: 186px; border-radius: 50%;
    background: var(--lime);
  }
  .front-name {
    position: absolute; left: 296px; top: 162px; width: 500px;
    color: var(--ink-light); font-weight: 700; font-size: 50px; line-height: 1.1;
  }
  .card--front .rule-thin { top: 432px; }

  /* Back */
  .back-name {
    position: absolute; left: 38px; top: 48px;
    color: var(--ink-light); font-weight: 700; font-size: 30px; line-height: 1.1;
  }
  .person {
    position: absolute; left: 40px; top: 200px;
    display: flex; gap: 12px; align-items: stretch;
  }
  .person__bar { width: 14px; border-radius: 7px; background: var(--lime); }
  .person__name { color: var(--ink-light); font-size: 28px; font-weight: 500; line-height: 1.1; }
  .person__role { color: var(--ink-soft); font-size: 20px; line-height: 1.2; margin-top: 2px; }
  .card--back .rule-thin { top: 262px; height: 3px; }
  .back-mark {
    position: absolute; left: 496px; top: 146px;
    width: 236px; height: 236px; border-radius: 50%;
    background: var(--lime);
  }
  .contacts {
    position: absolute; left: 40px; top: 290px;
    list-style: none; color: var(--ink-light); font-size: 16.5px;
  }
  .contacts li { display: flex; align-items: center; gap: 8px; height: 24px; margin-bottom: 22px; }
  .contacts svg { width: 20px; height: 20px; flex: none; }
  .contacts .licence { padding-left: 30px; }
  .card--back .band-base { height: 24px; }
</style>
</head>
<body>
  <section class="card card--front" aria-label="Card front">
    <div class="front-mark"></div>
    <div class="front-name">Meridian Crestline Motors</div>
    <div class="rule-thin"></div>
    <div class="band-base"></div>
  </section>

  <section class="card card--back" aria-label="Card back">
    <div class="back-name">Meridian Crestline Motors</div>
    <div class="rule-thin"></div>
    <div class="back-mark"></div>
    <div class="person">
      <div class="person__bar"></div>
      <div>
        <div class="person__name">Darnell R Okonski</div>
        <div class="person__role">Owner</div>
      </div>
    </div>
    <ul class="contacts">
      <li>
        <svg viewBox="0 0 24 24" aria-hidden="true"><path fill="#a4c812" d="M6.6 10.8a15.1 15.1 0 0 0 6.6 6.6l2.2-2.2c.3-.3.7-.4 1-.2 1.1.4 2.3.6 3.6.6.6 0 1 .4 1 1V20c0 .6-.4 1-1 1C10.6 21 3 13.4 3 4c0-.6.4-1 1-1h3.5c.6 0 1 .4 1 1 0 1.3.2 2.5.6 3.6.1.3 0 .7-.2 1z"/></svg>
        (555) 304-6618
      </li>
      <li>
        <svg viewBox="0 0 24 24" aria-hidden="true"><rect x="3" y="5" width="18" height="14" rx="1.5" fill="none" stroke="#a4c812" stroke-width="2"/><path d="M3.5 6l8.5 7 8.5-7M3.5 18l6-6M20.5 18l-6-6" fill="none" stroke="#a4c812" stroke-width="2"/></svg>
        mercrestmotors@quillbox.example
      </li>
      <li class="licence">Dealer Lic # 48265</li>
    </ul>
    <div class="band-base"></div>
  </section>
</body>
</html>
```